Weightloss company needs Business Card

We want a business card that is clean and professional, yet portrays that we are a friendly, innovative, and versatile program designed to fit the needs of our clients.
I would like there to be 2 sides, one side having an appointment card, and the other side containing the logo and business information. There can be decorations on both sides. The logo is attached.

Target Market(s)

Men and women 40-60

Industry/Entity Type

Business

Contact Information for Business Card

Font styles to use
Sans Serif

Requirements
Must have
• The logo, space for business information
Nice to have
• The colors in the logo
Should not have
• No pictures of people or food

```html
<!DOCTYPE html>
<html lang="en">
<head>
<meta charset="utf-8">
<title>BrightTurn Wellness – Business Card</title>
<link rel="stylesheet" href="https://fonts.googleapis.com/css2?family=Source+Sans+3:wght@400;600;700&display=swap">
<style>
  :root {
    --brand-red: #ff0033;
    --paper: #ffffff;
    --ink: #111111;
    --backdrop: #2b2d31;
    --on-red: #ffffff;
  }
  * { box-sizing: border-box; margin: 0; padding: 0; }
  html, body {
    width: 1200px; height: 864px; overflow: hidden;
    background: var(--backdrop);
    font-family: "Source Sans 3", Arial, sans-serif;
  }
  .card {
    position: absolute;
    width: 600px; height: 340px;
    left: 300px;
    border-radius: 3px;
    box-shadow: 0 10px 24px rgba(0,0,0,.45);
  }
  .card--appointment { top: 60px; background: var(--paper); color: var(--brand-red); }
  .card--contact { top: 464px; background: var(--brand-red); color: var(--on-red); }

  /* brand name block */
  .brand {
    position: absolute; top: 44px; right: 44px;
    display: flex; align-items: center; gap: 10px;
  }
  .brand__dot {
    width: 34px; height: 34px; border-radius: 50%;
    background: currentColor;
  }
  .brand__name {
    font-weight: 700; font-size: 26px; line-height: 1;
    letter-spacing: -.3px;
  }

  /* appointment side */
  .appointment__title {
    position: absolute; left: 90px; top: 100px;
    font-size: 18px; font-weight: 600; letter-spacing: .2px;
  }
  .field {
    position: absolute; left: 84px;
    display: flex; align-items: flex-end;
    font-size: 14px; font-weight: 600;
  }
  .field--name { top: 134px; }
  .field--date { top: 166px; }
  .field--time { top: 198px; }
  .field__fill {
    display: inline-block; height: 12px;
    border-bottom: 2px dotted var(--ink);
    margin-left: 4px;
  }
  .field__suffix { color: var(--ink); font-size: 13px; margin: 0 2px; }
  .notice {
    position: absolute; left: 12px; right: 12px; top: 236px;
    display: flex; align-items: center; gap: 6px;
    font-size: 13.5px; font-weight: 600;
  }
  .notice__rule { height: 1px; background: var(--brand-red); }
  .notice__rule--lead { width: 80px; }
  .notice__rule--tail { flex: 1; margin-top: 22px; }
  .notice__text { white-space: nowrap; }

  /* contact side */
  .person { position: absolute; left: 74px; top: 138px; }
  .person__name { font-size: 21px; font-weight: 600; line-height: 1.1; }
  .person__role { font-size: 14px; line-height: 1.2; }
  .address {
    position: absolute; left: 64px; top: 196px;
    font-size: 14.5px; line-height: 1.2; font-style: normal;
  }
  .contacts {
    position: absolute; left: 50px; top: 250px;
    list-style: none; font-size: 14.5px; line-height: 1.3;
  }
  .contacts li { display: flex; align-items: center; gap: 10px; }
  .contacts svg { width: 11px; height: 11px; fill: var(--on-red); stroke: var(--on-red); }
</style>
</head>
<body>

<section class="card card--appointment" aria-label="Appointment side">
  <div class="brand">
    <span class="brand__name">BrightTurn Wellness</span>
    <span class="brand__dot"></span>
  </div>
  <h2 class="appointment__title">YOUR NEXT APPOINTMENT IS</h2>
  <div class="field field--name">Name:<span class="field__fill" style="width:226px"></span></div>
  <div class="field field--date">Date:<span class="field__fill" style="width:246px"></span></div>
  <div class="field field--time">Time:<span class="field__fill" style="width:96px"></span><span class="field__suffix">AM</span><span class="field__fill" style="width:100px;margin-left:0"></span><span class="field__suffix">PM</span></div>
  <div class="notice">
    <span class="notice__rule notice__rule--lead"></span>
    <span class="notice__text">If unable to keep appointment, kindly give 24hrs notice.</span>
    <span class="notice__rule notice__rule--tail"></span>
  </div>
</section>

<section class="card card--contact" aria-label="Contact side">
  <div class="brand">
    <span class="brand__name">BrightTurn Wellness</span>
    <span class="brand__dot"></span>
  </div>
  <div class="person">
    <p class="person__name">Daniel Hart</p>
    <p class="person__role">Managing Director</p>
  </div>
  <address class="address">12345, Address Goes Here<br>Country Name, 123456.</address>
  <ul class="contacts">
    <li><svg viewBox="0 0 12 12"><path stroke="none" d="M2.5 0.5l2 2.2-1.1 1.4c.7 1.5 2 2.8 3.5 3.5l1.4-1.1 2.2 2-1.3 2C5.5 10.3 1.7 6.5 .5 1.8z"/></svg>044-555 010 203</li>
    <li><svg viewBox="0 0 12 12"><rect x="0.5" y="2" width="11" height="8" stroke="none"/><path d="M1 2.6l5 4 5-4" fill="none" stroke="#ff0033" stroke-width="1"/></svg>hello@brightturn.com</li>
    <li><svg viewBox="0 0 12 12"><path d="M5 7l2-2M4.2 5.2L2.6 6.8a1.8 1.8 0 0 0 2.6 2.6l1.6-1.6M7.8 6.8l1.6-1.6a1.8 1.8 0 0 0-2.6-2.6L5.2 4.2" fill="none" stroke-width="1.3" stroke-linecap="round"/></svg>www.brightturn.com</li>
  </ul>
</section>

</body>
</html>
```